Presentation pour application de menu digitale

Je souhaite créer un flyer de présentation pour une application de menu digitale afin de la présenter à mes futurs clients. Cette application aura aussi vocation de premier réseau social culinaire pour les utilisateurs finaux.
Merci de récupérer le texte du site platovia.app
Le flyer sera imprimé au format A3 pliable pour en faire un format A4.
Le logo et les images que vous récupérerez seront en vernis sélectif.

Target Market(s)

restaurateur

Industry/Entity Type

Restaurateur

Font styles to use
Sans Serif

Colors
59FF00
82FF00
B8FF75
E3FFCB
F4FFEA
6B429C
8869AF
B7A5CE
E3DAEB
F3F0F8

```html
<!DOCTYPE html>
<html lang="fr">
<head>
<meta charset="utf-8">
<title>Platovia – dépliant et cartes de visite</title>
<link rel="stylesheet" href="https://fonts.googleapis.com/css2?family=Quicksand:wght@400;500;600;700&display=swap">
<style>
  :root{
    --purple:#6B429C;
    --purple-mid:#8869AF;
    --purple-soft:#B7A5CE;
    --purple-pale:#E3DAEB;
    --purple-mist:#F3F0F8;
    --mint:#7FD8BE;
    --ink:#3A3A40;
    --grey:#E6E6EA;
    --stage:#EDEDF0;
    --white:#FFFFFF;
    --font:'Quicksand', sans-serif;
  }
  *{box-sizing:border-box;margin:0;padding:0}
  html,body{width:1200px;height:435px;overflow:hidden;background:var(--stage);font-family:var(--font)}
  .canvas{position:relative;width:1200px;height:435px}

  .spread{position:absolute;top:86px;width:372px;height:263px;display:flex;box-shadow:0 4px 14px rgba(60,40,90,.18)}
  .spread--outer{left:24px}
  .spread--inner{left:420px}
  .panel{position:relative;width:186px;height:263px;overflow:hidden;background:var(--white)}
  .layer{position:absolute;left:0;top:0;width:100%;height:100%}
  .abs{position:absolute}

  .url{position:absolute;font-size:5px;font-weight:600;letter-spacing:.2px}
  .brand{display:flex;align-items:center;gap:3px;font-weight:700;color:var(--purple)}
  .brand__dot{border-radius:50%;background:var(--mint)}

  /* back panel */
  .features__title{left:0;top:8px;width:100%;text-align:center;color:var(--white);font-size:10px;font-weight:700}
  .features__sub{font-size:6px;font-weight:700}
  .features__list{list-style:none;font-size:4.2px;line-height:1.35}
  .features__list li{margin-bottom:2.5px;padding-left:4px;position:relative}
  .features__list li::before{content:"";position:absolute;left:0;top:1.6px;width:2px;height:2px;border-radius:50%;background:currentColor}
  .on-purple{color:var(--white)}
  .on-white{color:var(--purple)}
  .media{border-radius:3px}

  /* cover */
  .cover__kicker{left:14px;top:26px;color:var(--purple);font-size:7px;font-weight:500}
  .cover__title{left:12px;top:33px;color:var(--purple);font-size:21px;font-weight:500;letter-spacing:.5px;line-height:1}
  .cover__sub{left:14px;top:55px;color:var(--purple);font-size:6.4px;font-weight:500;letter-spacing:.6px}
  .phone{position:absolute;border-radius:9px;background:#1F1F24;padding:3px;box-shadow:0 3px 6px rgba(0,0,0,.25)}
  .phone__screen{width:100%;height:100%;border-radius:7px}
  .store-badge{position:absolute;width:46px;height:13px;border-radius:3px;background:#1F1F24}

  /* inner left */
  .intro{left:12px;top:12px;width:162px;color:var(--purple-mid);font-size:4.2px;line-height:1.45}
  .intro p+p{margin-top:4px}
  .mission__title{left:14px;top:110px;color:var(--white);font-size:11px;font-weight:700}
  .mission__text{left:14px;top:128px;width:150px;color:var(--white);font-size:4.2px;line-height:1.45}

  /* inner right */
  .how__title{left:0;top:12px;width:100%;text-align:center;color:var(--white);font-size:10.5px;font-weight:700}
  .step{position:absolute;left:12px;width:164px;display:flex;gap:6px;align-items:flex-start}
  .step__icon{flex:0 0 18px;height:18px;border-radius:3px}
  .step__body h3{font-size:6px;font-weight:700}
  .step__body p{font-size:4.2px;line-height:1.35;margin-top:1px}
  .step--light{color:var(--white)}
  .step--light .step__icon{background:var(--purple-pale)}
  .step--dark{color:var(--purple)}
  .step--dark .step__icon{background:var(--white)}

  /* business cards */
  .card{position:absolute;left:851px;width:290px;height:166px;border-radius:14px;background:var(--white);box-shadow:0 4px 12px rgba(0,0,0,.14);overflow:hidden}
  .card--front{top:36px}
  .card--back{top:233px}
  .card__brand{position:absolute;font-size:19px}
  .card--front .card__brand{left:50%;top:52px;transform:translateX(-50%)}
  .card__rule{position:absolute;left:24px;right:24px;top:112px;height:4px;background:linear-gradient(90deg,var(--ink) 0 28%,var(--mint) 28% 72%,var(--ink) 72%)}
  .card__url{position:absolute;left:0;width:100%;top:122px;text-align:center;font-size:7px;letter-spacing:2.5px;color:var(--ink);font-weight:500}
  .card--back .card__brand{left:24px;top:68px;font-size:17px}
  .card__bar{position:absolute;left:150px;top:26px;width:14px;height:116px}
  .card__name{position:absolute;left:176px;top:26px;color:var(--ink);font-size:14px;font-weight:700;line-height:1}
  .card__role{position:absolute;left:176px;top:42px;color:var(--ink);font-size:6.5px;font-weight:500}
  .card__contact{position:absolute;left:176px;top:66px;list-style:none;color:var(--ink);font-size:6.5px;line-height:1.6;font-weight:500}
</style>
</head>
<body>
<main class="canvas">

  <!-- outer side of the folded leaflet -->
  <section class="spread spread--outer" aria-label="Dépliant, face extérieure">
    <article class="panel panel--features">
      <svg class="layer" viewBox="0 0 186 263" aria-hidden="true">
        <path d="M0 0H186V92L0 118Z" fill="var(--purple)"/>
        <path d="M0 236L186 226V263H0Z" fill="var(--purple)"/>
      </svg>
      <h2 class="abs features__title">Fonctionnalités</h2>
      <h3 class="abs features__sub on-purple" style="left:12px;top:26px">Pour les clients</h3>
      <ul class="abs features__list on-purple" style="left:12px;top:36px;width:86px">
        <li>Accès instantané au menu par QR code.</li>
        <li>Sauvegarde de vos plats préférés.</li>
        <li>Avis et photos partagés entre gourmets.</li>
      </ul>
      <div class="abs media" role="img" aria-label="Ordinateur portable affichant l'application" style="left:108px;top:30px;width:64px;height:38px;background:linear-gradient(135deg,#DCDCE2,#F6F6F8)"></div>
      <ul class="abs features__list on-purple" style="left:108px;top:72px;width:70px">
        <li>Personnalisation avancée de chaque commande.</li>
      </ul>
      <h3 class="abs features__sub on-white" style="left:12px;top:122px">Pour les restaurateurs</h3>
      <ul class="abs features__list on-white" style="left:12px;top:132px;width:80px">
        <li>Menu modifiable en temps réel.</li>
        <li>Analyse des plats les plus commandés.</li>
      </ul>
      <div class="abs" role="img" aria-label="Deux téléphones affichant le menu" style="left:24px;top:162px;width:56px;height:56px;border-radius:50%;border:1.5px solid var(--purple);background:radial-gradient(circle,#F2F2F5,#DADAE2)"></div>
      <ul class="abs features__list on-white" style="left:100px;top:150px;width:76px">
        <li>Visibilité auprès d'une communauté active.</li>
        <li>Promotion ciblée auprès des utilisateurs proches.</li>
      </ul>
      <span class="url" style="left:60px;top:246px;color:var(--white)">www.platovia.app</span>
    </article>

    <article class="panel panel--cover">
      <svg class="layer" viewBox="0 0 186 263" aria-hidden="true">
        <path d="M0 140C40 150 90 120 120 100C150 82 170 80 186 78V263H0Z" fill="var(--purple)"/>
      </svg>
      <span class="abs cover__kicker">Le 1er</span>
      <h1 class="abs cover__title">RÉSEAU</h1>
      <span class="abs cover__sub">SOCIAL CULINAIRE</span>
      <div class="abs brand" style="right:10px;top:12px;font-size:9px">
        <span class="brand__dot" style="width:8px;height:8px"></span>Platovia
      </div>
      <div class="phone" style="left:18px;top:92px;width:64px;height:128px">
        <div class="phone__screen" role="img" aria-label="Grille de photos de plats dans l'application" style="background:linear-gradient(160deg,#C9A98A,#8E9C6A 45%,#D98A7A)"></div>
      </div>
      <div class="phone" style="left:90px;top:74px;width:56px;height:114px">
        <div class="phone__screen" style="background:var(--white);display:flex;align-items:center;justify-content:center">
          <span class="brand" style="font-size:7px"><span class="brand__dot" style="width:6px;height:6px"></span>Platovia</span>
        </div>
      </div>
      <div class="store-badge" style="left:128px;top:204px" aria-label="Badge boutique d'applications"></div>
      <div class="store-badge" style="left:128px;top:222px" aria-label="Badge boutique d'applications"></div>
      <span class="url" style="left:20px;top:246px;color:var(--white)">www.platovia.app</span>
    </article>
  </section>

  <!-- inner side of the folded leaflet -->
  <section class="spread spread--inner" aria-label="Dépliant, face intérieure">
    <article class="panel panel--mission">
      <div class="abs intro">
        <p>Plongez au cœur d'une révolution culinaire où chaque repas devient une expérience à partager. Notre menu digital relie les restaurants et leurs clients dans un espace simple, rapide et convivial.</p>
        <p>Parcourez les cartes, découvrez les plats recommandés par la communauté et gardez vos coups de cœur à portée de main, le tout depuis votre téléphone.</p>
      </div>
      <svg class="layer" viewBox="0 0 186 263" aria-hidden="true">
        <path d="M0 112L186 92V150L0 172Z" fill="var(--purple-mid)"/>
      </svg>
      <div class="abs" role="img" aria-label="Bols d'ingrédients frais vus de dessus" style="left:0;top:0;width:186px;height:263px;clip-path:polygon(0 65%,100% 57%,100% 100%,0 100%);background:linear-gradient(135deg,#3E3A36,#7A8C4A 40%,#B5443C 70%,#E8C7C9)"></div>
      <h2 class="abs mission__title">Notre mission</h2>
      <p class="abs mission__text">Rendre chaque sortie au restaurant plus fluide et plus connectée, en offrant aux gourmets un outil clair et aux restaurateurs un lien direct avec leur clientèle.</p>
    </article>

    <article class="panel panel--how">
      <svg class="layer" viewBox="0 0 186 263" aria-hidden="true">
        <rect width="186" height="170" fill="var(--purple)"/>
        <path d="M0 70H186V170H0Z" fill="var(--purple-mid)" opacity=".35"/>
        <rect y="170" width="186" height="93" fill="var(--grey)"/>
      </svg>
      <h2 class="abs how__title">Comment ça marche?</h2>
      <div class="step step--light" style="top:38px">
        <div class="step__icon"></div>
        <div class="step__body"><h3>1. Scannez le QR code</h3><p>À votre arrivée, scannez le code pour débloquer le menu interactif de votre restaurant.</p></div>
      </div>
      <div class="step step--light" style="top:82px">
        <div class="step__icon"></div>
        <div class="step__body"><h3>2. Découvrez</h3><p>À votre arrivée, scannez le code pour débloquer le menu interactif de votre restaurant.</p></div>
      </div>
      <div class="step step--light" style="top:126px">
        <div class="step__icon"></div>
        <div class="step__body"><h3>3. Choisissez</h3><p>Préparez votre commande.</p></div>
      </div>
      <div class="step step--dark" style="top:178px">
        <div class="step__icon"></div>
        <div class="step__body"><h3>4. Personnaliser et sauvegardez</h3><p>Sélectionnez et personnalisez vos plats, sauvegardez vos favoris pour la prochaine fois, et partagez vos choix avec vos amis.</p></div>
      </div>
      <div class="step step--dark" style="top:210px">
        <div class="step__icon"></div>
        <div class="step__body"><h3>5. Partagez votre expérience</h3><p>Devenez une partie de notre réseau social de gourmets, recommandez des plats et découvrez les favoris d'autres utilisateurs.</p></div>
      </div>
      <span class="url" style="left:66px;top:248px;color:var(--purple)">www.platovia.app</span>
    </article>
  </section>

  <!-- business cards -->
  <article class="card card--front" aria-label="Carte de visite, recto">
    <div class="brand card__brand"><span class="brand__dot" style="width:14px;height:14px"></span>Platovia</div>
    <div class="card__rule"></div>
    <span class="card__url">www.platovia.app</span>
  </article>

  <article class="card card--back" aria-label="Carte de visite, verso">
    <div class="brand card__brand"><span class="brand__dot" style="width:12px;height:12px"></span>Platovia</div>
    <svg class="card__bar" viewBox="0 0 14 116" aria-hidden="true">
      <circle cx="7" cy="6" r="3" fill="var(--mint)"/>
      <path d="M2 16a5 5 0 0 1 10 0z" fill="var(--mint)"/>
      <rect x="0" y="34" width="14" height="82" rx="7" fill="var(--mint)"/>
      <path d="M4.5 44c0 4 3 7 5 7l1-1.8-2-1-1 .8c-1-.5-1.8-1.3-2.2-2.3l.8-1-1-2z" fill="#fff"/>
      <rect x="3.5" y="62" width="7" height="5" rx=".8" fill="none" stroke="#fff" stroke-width=".9"/>
      <path d="M3.5 62.5L7 65l3.5-2.5" fill="none" stroke="#fff" stroke-width=".9"/>
      <circle cx="7" cy="82" r="3.6" fill="none" stroke="#fff" stroke-width=".9"/>
      <path d="M3.4 82h7.2M7 78.4c-1.6 2-1.6 5.2 0 7.2M7 78.4c1.6 2 1.6 5.2 0 7.2" fill="none" stroke="#fff" stroke-width=".6"/>
      <path d="M7 96a3 3 0 0 1 3 3c0 2.2-3 5-3 5s-3-2.8-3-5a3 3 0 0 1 3-3z" fill="#fff"/>
      <circle cx="7" cy="99" r="1" fill="var(--mint)"/>
    </svg>
    <span class="card__name">Camille Arnaud</span>
    <span class="card__role">Designation</span>
    <ul class="card__contact">
      <li>+33 1 84 60 27 15</li>
      <li>+33 6 12 48 90 33</li>
      <li>contact@platovia.app</li>
      <li>www.platovia.app</li>
      <li>your address here</li>
      <li>City, Zip Code</li>
    </ul>
  </article>

</main>
</body>
</html>
```